Print on top the name of the company: (Or Similar)
Lumora Cleaning & Disinfecting
Because your standards aren't standard.

We adhere to ALL QRV guidelines for both residential and commercial cleaning.

Infection Control is our ultimate goal.

Instructions:
Opening a residential and commercial cleaning and disinfecting company in south Florida.

Targeting high-end residential clients, commercial and healthcare facilities, specializing in Ambulatory Care Guidelines. With a concentration and expertise in targeting Covid 19 and other transmissible pathogens.

WELM trained.
Owned and operated by a licensed BSN Registered Nurse specially ​trained in Infection Control Prevention with over 25 years experience. Over two decades in Ambulatory Surgery Center Administration, Director of Nursing and Infection Control Prevention ad Consulting.

Looking to create a business flier that emphasizes Cleaning & Disinfection
along with the standard expectation for residential and Commercial cleaning services

Target Market(s)

Residential & Commercial

Font styles to use
Decorative

Requirements
Must have
• A checklist for cleaning services

```html
<!DOCTYPE html>
<html lang="en">
<head>
<meta charset="utf-8">
<title>Lumora Cleaning &amp; Disinfecting</title>
<link href="https://fonts.googleapis.com/css2?family=Montserrat:wght@300;400;500;700;800&display=swap" rel="stylesheet">
<style>
  :root {
    --navy: #1b1d4b;
    --blue: #3a6aaa;
    --ribbon: #386aa8;
    --ribbon-dark: #1d2450;
    --deep: #1c3f73;
    --panel: #ffffff;
    --card: #dedede;
    --ink: #222226;
  }
  * { margin: 0; padding: 0; box-sizing: border-box; }
  html, body { width: 856px; height: 1200px; overflow: hidden; background: #fff; }
  body { font-family: "Montserrat", sans-serif; color: var(--ink); }
  .flyer { position: relative; width: 856px; height: 1200px; overflow: hidden; background: #fff; }

  .hero-photo {
    position: absolute; left: 430px; top: 0; width: 426px; height: 365px;
    background: linear-gradient(90deg, #ffffff 0%, #e9eef4 18%, #cdd8e4 45%, #9fb2c4 75%, #3e4c58 100%);
  }
  .backdrop {
    position: absolute; left: 0; top: 365px; width: 856px; height: 835px;
    background: linear-gradient(180deg, #2a5188 0%, #1f3f72 45%, #1a2f5a 100%);
  }

  .brand { position: absolute; left: 30px; top: 44px; color: var(--navy); font-weight: 800; line-height: 1; }
  .brand-top { font-size: 40px; letter-spacing: 0.3px; }
  .brand-bottom { font-size: 53px; margin-top: 2px; }
  .goal { position: absolute; left: 30px; top: 139px; color: var(--blue); font-weight: 800; font-size: 39.5px; line-height: 40px; }
  .rule { position: absolute; left: 30px; top: 238px; width: 127px; height: 4px; background: var(--navy); }
  .standard { position: absolute; left: 30px; top: 260px; color: var(--navy); font-weight: 700; font-size: 19.5px; line-height: 24.5px; }

  .panel { position: absolute; left: 73px; top: 365px; width: 710px; height: 811px; background: var(--panel); }

  .ribbon { position: absolute; left: 49px; width: 318px; height: 43px; }
  .ribbon svg { position: absolute; left: 0; top: 0; }
  .ribbon span { position: absolute; left: 46px; top: 5px; color: #fff; font-weight: 300; font-size: 26px; letter-spacing: 1px; }
  .ribbon-instructions { top: 338px; }
  .ribbon-trained { top: 487px; }

  .copy { position: absolute; left: 95px; width: 670px; font-size: 12.4px; line-height: 19.6px; color: #1f1f22; }
  .copy-instructions { top: 395px; }
  .copy-trained { top: 546px; }

  .service-card { position: absolute; top: 662px; width: 319px; height: 397px; background: var(--card); border-radius: 0 0 34px 34px; text-align: center; }
  .service-card.commercial { left: 95px; }
  .service-card.residential { left: 438px; }
  .service-icon { display: block; margin: 17px auto 0; }
  .service-card h2 { font-weight: 800; font-size: 28px; color: var(--blue); letter-spacing: 0.8px; margin-top: 5px; line-height: 32px; }
  .service-card ul { list-style: none; margin-top: 5px; }
  .service-card li { font-size: 18px; line-height: 30.3px; color: var(--ink); }

  .call-band { position: absolute; left: 40px; top: 1058px; width: 776px; height: 80px; background: var(--deep); color: #fff; font-weight: 700; font-size: 31px; letter-spacing: 1px; text-align: center; line-height: 80px; box-shadow: 0 6px 8px rgba(0,0,0,0.25); }
</style>
</head>
<body>
<div class="flyer">
  <div class="hero-photo" role="img" aria-label="Photo of a worker in a white protective suit spraying disinfectant in a bright glass corridor"></div>
  <div class="backdrop" role="img" aria-label="Blurred dark blue interior photo background"></div>

  <h1 class="brand">
    <div class="brand-top">LUMORA CLEANING</div>
    <div class="brand-bottom">&amp; DISINFECTING</div>
  </h1>
  <div class="goal">INFECTION CONTROL IS<br>OUR ULTIMATE GOAL</div>
  <div class="rule"></div>
  <p class="standard">We adhere to ALL QRV guidelines for both<br>residential and commercial cleaning.</p>

  <div class="panel"></div>

  <div class="ribbon ribbon-instructions">
    <svg width="318" height="56" viewBox="0 0 318 56"><polygon points="0,43 24,43 24,56" fill="var(--ribbon-dark)"/><polygon points="0,0 301,0 318,43 0,43" fill="var(--ribbon)"/></svg>
    <span>INSTRUCTIONS:</span>
  </div>
  <p class="copy copy-instructions">Opening a residential and commercial cleaning and disinfecting company in south Florida.<br>Targeting high-end residential clients, commercial and healthcare facilities, specializing in Ambulatory Care Guidelines. With a concentration and expertise in targeting Covid 19 and other transmissible pathogens.</p>

  <div class="ribbon ribbon-trained">
    <svg width="318" height="56" viewBox="0 0 318 56"><polygon points="0,43 24,43 24,56" fill="var(--ribbon-dark)"/><polygon points="0,0 301,0 318,43 0,43" fill="var(--ribbon)"/></svg>
    <span>WELM TRAINED</span>
  </div>
  <p class="copy copy-trained">Owned and operated by a licensed BSN Registered Nurse specially trained in Infection Control Prevention with over 25 years experience.<br>Over two decades in Ambulatory Surgery Center Administration, Director of Nursing and Infection Control Prevention ad Consulting.</p>

  <section class="service-card commercial">
    <svg class="service-icon" width="76" height="76" viewBox="0 0 76 76"><circle cx="38" cy="38" r="38" fill="var(--ribbon)"/><g fill="none" stroke="#fff" stroke-width="2"><rect x="33" y="16" width="22" height="14"/><line x1="44" y1="30" x2="44" y2="35"/><line x1="16" y1="35" x2="60" y2="35"/><rect x="18" y="35" width="12" height="24"/><line x1="18" y1="43" x2="30" y2="43"/><line x1="18" y1="51" x2="30" y2="51"/><line x1="58" y1="35" x2="58" y2="59"/><rect x="19" y="20" width="6" height="12"/><rect x="38" y="40" width="12" height="10" rx="2"/><line x1="44" y1="50" x2="44" y2="57"/><line x1="38" y1="58" x2="50" y2="58"/></g></svg>
    <h2>COMMERCIAL</h2>
    <ul>
      <li>Janitorial</li>
      <li>Offices</li>
      <li>Floor Maintenance</li>
      <li>Carpet Cleaning</li>
      <li>Move - Ins</li>
      <li>Move - Outs</li>
      <li>Constructions Clean - Ups</li>
      <li>Estate Clean - Outs</li>
    </ul>
  </section>

  <section class="service-card residential">
    <svg class="service-icon" width="76" height="76" viewBox="0 0 76 76"><circle cx="38" cy="38" r="38" fill="var(--ribbon)"/><g fill="none" stroke="#fff" stroke-width="2"><rect x="33" y="16" width="22" height="14"/><line x1="44" y1="30" x2="44" y2="35"/><line x1="16" y1="35" x2="60" y2="35"/><rect x="18" y="35" width="12" height="24"/><line x1="18" y1="43" x2="30" y2="43"/><line x1="18" y1="51" x2="30" y2="51"/><line x1="58" y1="35" x2="58" y2="59"/><rect x="19" y="20" width="6" height="12"/><rect x="38" y="40" width="12" height="10" rx="2"/><line x1="44" y1="50" x2="44" y2="57"/><line x1="38" y1="58" x2="50" y2="58"/></g></svg>
    <h2>RESIDENTIAL</h2>
    <ul>
      <li>House Cleaning</li>
      <li>Before And After Party</li>
      <li>Move - Ins</li>
      <li>Move - Outs</li>
      <li>Holiday Cleaning</li>
      <li>Seasonal Cleaning</li>
      <li>Carpet Cleaning</li>
      <li>Deodorizing And Aanitizing</li>
    </ul>
  </section>

  <div class="call-band">PLEASE CALL US AT: (555) 014 27 83</div>
</div>
</body>
</html>
```